Bonusheft für Patienten als kleine DIN A6 Broschüre
Zielgruppe
Bonusheft für Patienten als kleine DIN A6 Broschüre in der Zahn-Prophylaxe. Die Texte haben wir bereits vollständig formuliert, auch die Gliederung ist vorgegeben.
Wir sind eine Zahnarztpraxis mit dem Schwerpunkt Prophylaxe. Für unsere Prophylaxeabteilung möchten wir eine DIN A6 Broschüre entwerfen lassen, die als Bonusheft für Patienten dient.
Inhalt: Informationen über unsere Praxis, die leitende Mitarbeiterin, individuelle Risiken und Empfehlungen der Patienten. Auch Fakten und Tipps zur Verbesserung der Mundhygiene und Putzgewohnheiten werden Beschrieben.
Aufgabenstellung
Broschüre als DIN A6 Bonusheft mit circa sieben gestalteten Seiten, bei denen wir den Aufbau und die exakten Texte bereits vollständig vorgeben. Zusätzlich folgen mehrere gleiche Seiten, bei denen die Termine und Stempel eingetragen werden (ca. fünf Seiten).
Für Ihre Orientierung haben wir unsere Fotos und Farbschema von vorhandenen Designs unserer Praxis bereitgestellt.
Orientieren Sie sich gerne an unserer vorhandenen Homepage im Hinblick auf unseren Stil und das Praxislogo.
Homepage: www.zahnpflege-am-lindenbogen.de
Wir stellen einige Fotos zur Verwendung bereit. Falls nötig, verwenden Sie auch Stock Fotos.
Im folgenden werden wir den gewünschten Aufbau mit den Texten je Seite detailliert vorstellen. Ihre Aufgabe ist es, dies in ein modernes, frisches, ansprechendes und kompetentes Design umzusetzen.
1. Seite / Cover
- Mit Praxislogo
- Text: „Mein Prophylaxepass“
2. Seite:
- Überschrift: „Sie lassen nicht jeden an Ihre Zähne? Wir auch nicht.“
-Text: „Herzlich Willkommen! Mein Name ist Wiebke und ich arbeite als leitende Mitarbeiterin im Prophylaxe Zentrum Talbrück. Momentan befinde ich mich in der Weiterbildung zur Dentalhygienikerin und bin begeistert von der Arbeit in der präventiven Zahnmedizin. Mit meinem Wissen und meiner Erfahrung möchte ich dazu beitragen, dass unsere Patienten sich bei uns wohl und gut betreut fühlen. Ich freue mich darauf, Ihnen zu helfen, Ihre Zahngesundheit zu erhalten und zu verbessern!“
- Foto einer Mitarbeiterin
4. Seite:
- Überschrift: „Die professionelle Zahnreinigung – Wellness & Prävention“
- Text: „Eine wichtige Präventionsmaßnahme ist die regelmäßige Zahnreinigung in unserem Prophylaxe-Zentrum. Karies, Mundgeruch und Zahnfleischerkrankungen werden effektiv vorgebeugt. Die Zahnreinigung ist ein Teil der individuell geplanten Prophylaxe und eine sinnvolle Ergänzung der häus..

```html
<!DOCTYPE html>
<html lang="de">
<head>
<meta charset="utf-8">
<title>Mein Prophylaxepass – Bonusheft</title>
<link rel="stylesheet" href="https://fonts.googleapis.com/css2?family=Exo+2:wght@600;700;800&family=Open+Sans:wght@400;600;700&display=swap">
<style>
  :root{
    --canvas:#ececec;
    --paper:#f8f8f7;
    --paper-shade:#efefed;
    --beige:#c8c1a3;
    --beige-dark:#b3aa86;
    --beige-light:#e6e1d0;
    --ink:#3a3a3a;
    --ink-soft:#6b6b6b;
    --muted:#a9a9a9;
    --sky:#bfe0ea;
    --sky-deep:#8cc3d4;
    --brick:#a77d62;
  }
  *{box-sizing:border-box;margin:0;padding:0}
  html,body{width:1200px;height:4032px;overflow:hidden}
  body{background:var(--canvas);font-family:"Open Sans",sans-serif;color:var(--ink);position:relative}

  .panel{position:absolute;left:0;width:1200px;height:806px}
  .panel:nth-of-type(1){top:0}
  .panel:nth-of-type(2){top:806px}
  .panel:nth-of-type(3){top:1612px}
  .panel:nth-of-type(4){top:2418px}
  .panel:nth-of-type(5){top:3224px}

  .page{position:absolute;width:396px;height:560px;background:var(--paper);overflow:hidden;box-shadow:0 10px 30px rgba(0,0,0,.08)}
  .spread .page.left{left:204px;top:123px;background:linear-gradient(90deg,var(--paper) 85%,var(--paper-shade))}
  .spread .page.right{left:600px;top:123px;background:linear-gradient(90deg,var(--paper-shade),var(--paper) 15%)}
  .page-no{position:absolute;top:18px;right:24px;font-family:"Exo 2",sans-serif;font-weight:700;font-size:26px;color:var(--beige-light)}
  .page.left .page-no{right:24px}
  .page-url{position:absolute;bottom:16px;left:28px;font-size:7px;color:var(--muted);letter-spacing:.3px}

  .kicker,.headline{font-family:"Exo 2",sans-serif;font-weight:800;text-transform:uppercase;line-height:1.05}
  .kicker{color:var(--beige);font-size:20px}
  .headline{color:var(--ink);font-size:21px}
  .copy{font-size:8.6px;line-height:1.55;color:var(--ink-soft)}
  .copy.strong{font-weight:700;color:var(--ink);font-size:9px}

  .photo{position:absolute}

  /* cover */
  .cover{left:380px;top:92px;width:440px;height:622px}
  .cover .photo{left:0;top:0;width:440px;height:400px;background:linear-gradient(180deg,var(--sky) 0%,#e3eef0 45%,#d9cfbf 75%,#cbbfa8 100%)}
  .cover .building{position:absolute;right:0;top:70px;width:250px;height:330px;background:linear-gradient(160deg,var(--brick),#8d6a55);opacity:.55}
  .logo-box{position:absolute;left:0;top:40px;width:220px;height:92px;background:#fff;padding:18px 22px}
  .logo-name{display:flex;align-items:center;gap:10px;font-family:"Open Sans",sans-serif;font-weight:400;font-size:17px;color:var(--ink);line-height:1.1}
  .logo-name .mark{width:14px;height:14px;background:var(--beige);flex:none}
  .logo-sub{font-size:7.5px;color:var(--ink-soft);margin-top:8px;margin-left:24px}
  .cover-title{position:absolute;left:44px;top:440px}
  .cover-title .kicker{font-size:38px}
  .cover-title .headline{font-size:40px}
  .cover-band{position:absolute;left:0;bottom:0;width:100%;height:40px;background:var(--beige)}

  /* 02 / 03 */
  .intro{position:absolute;left:34px;top:58px;width:300px}
  .intro .headline{margin-top:4px;margin-bottom:14px}
  .staff-photo{right:0;bottom:0;width:170px;height:240px;background:linear-gradient(180deg,#d9d4cc,#4e7a6c 70%,#3d6457)}
  .pzr{position:absolute;left:30px;top:58px;width:330px}
  .pzr .headline{font-size:19px;margin:2px 0 12px}
  .pzr-band{position:absolute;left:0;top:280px;width:100%;height:150px;background:var(--beige)}
  .smile-photo{left:0;top:290px;width:190px;height:170px;background:linear-gradient(160deg,#dfe8ec,#e8d3b9 60%,#c9a97e)}
  .pzr-note{position:absolute;left:200px;top:300px;width:170px;background:#fff;padding:14px;font-size:7.6px;line-height:1.55;color:var(--ink-soft)}

  /* 04 / 05 */
  .team-photo{left:0;top:0;width:396px;height:210px;background:linear-gradient(180deg,#e9eef0,#c9d6dd 60%,#7e97a8)}
  .tech{position:absolute;left:34px;top:236px;width:320px}
  .tech .headline{margin:2px 0 14px}
  .risk{position:absolute;left:40px;top:70px}
  .risk .kicker{margin-bottom:22px}
  .checklist{list-style:none}
  .checklist li{display:flex;align-items:center;gap:14px;font-size:11px;color:var(--ink-soft);margin-bottom:12px}
  .checklist li::before{content:"";width:11px;height:11px;border:1px solid var(--beige-dark);flex:none}

  /* 06 / 07 */
  .tips{position:absolute;left:40px;top:90px}
  .tips .headline{margin:2px 0 22px}
  .tips .checklist li{margin-bottom:10px}
  .summary{position:absolute;left:0;top:34px;width:100%;background:var(--beige);padding:16px 30px}
  .summary .row{display:flex;align-items:center;gap:8px;font-size:7px;color:#fff;margin-bottom:8px}
  .summary .row:last-child{margin-bottom:0}
  .summary .input{flex:1;height:13px;background:#fff;border-radius:7px}
  .summary .opt::before{border-color:#fff;background:#fff}

  .entries{position:absolute;left:30px;width:336px}
  .entries.under-summary{top:160px}
  .entries.full{top:50px}
  .entry{margin-bottom:20px}
  .entry-title{font-size:7px;color:var(--ink-soft);margin-bottom:6px}
  .entry-row{display:flex;align-items:center;gap:10px;font-size:6.8px;color:var(--ink-soft);margin-bottom:6px}
  .lbl{width:40px;flex:none}
  .opt{display:inline-flex;align-items:center;gap:4px}
  .opt::before{content:"";width:9px;height:9px;border:1px solid var(--beige-dark);border-radius:50%}
  .stamp-row{display:flex;align-items:center;gap:8px;margin-bottom:5px}
  .pill{width:70px;height:14px;border-radius:7px;background:var(--beige);font-size:6.5px;color:#fff;display:flex;align-items:center;padding-left:8px;flex:none}
  .field{flex:1;height:1px;background:var(--beige-light)}
</style>
</head>
<body>

<!-- cover -->
<section class="panel">
  <article class="page cover">
    <div class="photo" role="img" aria-label="Foto des Praxisgebäudes aus Backstein unter hellem Himmel">
      <div class="building"></div>
    </div>
    <div class="logo-box">
      <div class="logo-name"><span class="mark"></span>Zahnpflege am Lindenbogen</div>
      <p class="logo-sub">Dr. Henrik &amp; Lars Ostermann mit Team</p>
    </div>
    <h1 class="cover-title"><span class="kicker">Mein</span><br><span class="headline">Prophylaxepass</span></h1>
    <div class="cover-band"></div>
  </article>
</section>

<!-- pages 02 / 03 -->
<section class="panel spread">
  <article class="page left">
    <span class="page-no">02</span>
    <div class="intro">
      <h2 class="kicker">Sie lassen nicht jeden an Ihre Zähne?</h2>
      <p class="headline">Wir auch nicht.</p>
      <p class="copy strong">„Herzlich Willkommen! Mein Name ist Wiebke und ich arbeite als leitende Mitarbeiterin im Prophylaxe Zentrum Talbrück. Momentan befinde ich mich in der Weiterbildung zur Dentalhygienikerin und bin begeistert von der Arbeit in der präventiven Zahnmedizin. Mit meinem Wissen und meiner Erfahrung möchte ich dazu beitragen, dass unsere Patienten sich bei uns wohl und gut betreut fühlen. Ich freue mich darauf, Ihnen zu helfen, Ihre Zahngesundheit zu erhalten und zu verbessern!“</p>
    </div>
    <div class="photo staff-photo" role="img" aria-label="Foto der leitenden Prophylaxe-Mitarbeiterin mit Zahnmodell"></div>
    <span class="page-url">www.zahnpflege-am-lindenbogen.de</span>
  </article>
  <article class="page right">
    <span class="page-no">03</span>
    <div class="pzr">
      <h2 class="kicker">Die professionelle Zahnreinigung</h2>
      <p class="headline">Wellness &amp; Prävention</p>
      <p class="copy">Eine wichtige Präventionsmaßnahme ist die regelmäßige Zahnreinigung in unserem Prophylaxe-Zentrum. Karies, Mundgeruch und Zahnfleischerkrankungen werden effektiv vorgebeugt. Die Zahnreinigung ist ein Teil der individuell geplanten Prophylaxe und eine sinnvolle Ergänzung der häuslichen Zahnpflege. Schonend werden alle Beläge und Verfärbungen entfernt, damit sich Ihre Zähne wieder glatt und frisch anfühlen.</p>
    </div>
    <div class="pzr-band"></div>
    <div class="photo smile-photo" role="img" aria-label="Foto einer lächelnden Patientin im Behandlungsstuhl"></div>
    <p class="pzr-note">Natürlich weiße Zähne? Nach der professionellen Zahnreinigung sieht man oft ihre natürliche Farbe wieder. Zusätzlich werden die Zähne poliert und mit Fluorid geschützt.</p>
  </article>
</section>

<!-- pages 04 / 05 -->
<section class="panel spread">
  <article class="page left">
    <div class="photo team-photo" role="img" aria-label="Foto des Praxisteams im Gespräch mit Patienten"></div>
    <div class="tech">
      <h2 class="kicker">Moderne Technik</h2>
      <p class="headline">Für eine bessere Behandlung</p>
      <p class="copy">Für unsere Prophylaxebehandlungen nutzen wir aktuelle Behandlungsmethoden und hochwertige Geräte. Dadurch gewährleisten wir für unsere Patienten eine feine und angenehme Behandlung. Gleichzeitig stellen wir eine gründliche Reinigung sicher, welche Ihre Zähne nachhaltig schützt und Krankheiten vorbeugt.</p>
    </div>
    <span class="page-url">www.zahnpflege-am-lindenbogen.de</span>
  </article>
  <article class="page right">
    <span class="page-no">05</span>
    <div class="risk">
      <h2 class="kicker">Risikoanalyse</h2>
      <ul class="checklist">
        <li>Kariesaktivität</li>
        <li>Empfindliches Zahnfleisch</li>
        <li>Erosionen / Säureschäden</li>
        <li>Zahnschmelzverlust</li>
        <li>Weicher Zahnschmelz</li>
        <li>Halitosis (Mundgeruch)</li>
        <li>Zahnverfärbungen</li>
        <li>Rauchen</li>
        <li>Retainer</li>
      </ul>
    </div>
  </article>
</section>

<!-- pages 06 / 07 -->
<section class="panel spread">
  <article class="page left">
    <span class="page-no">06</span>
    <div class="tips">
      <h2 class="kicker">Ergänzende</h2>
      <p class="headline">Pflegetipps</p>
      <ul class="checklist">
        <li>1. Zahnseide</li>
        <li>2. Superfloss</li>
        <li>3. Zahnseidesticks</li>
        <li>4. Interdentalbürstchen</li>
        <li>5. Zungenreinigung</li>
        <li>6. Intensiv Fluoridierung</li>
        <li>7. 1x wöchentlich Spezial Zahnpasta</li>
        <li>8. Munddusche</li>
        <li>9. Mundspüllösung</li>
      </ul>
    </div>
    <span class="page-url">www.zahnpflege-am-lindenbogen.de</span>
  </article>
  <article class="page right">
    <span class="page-no">07</span>
    <div class="summary">
      <div class="row">Prophylaxe-Pass übersicht von: <span class="input"></span></div>
      <div class="row">Mitarbeiter: <span class="input"></span></div>
      <div class="row">Re-Intervall: <span class="opt">3 Monate</span><span class="opt">4 Monate</span><span class="opt">6 Monate</span><span class="opt">12 Monate</span></div>
    </div>
    <div class="entries under-summary">
      <div class="entry">
        <p class="entry-title">Nächster Termin:</p>
        <div class="entry-row"><span class="lbl">Intervall:</span><span class="opt">3 Monate</span><span class="opt">4 Monate</span><span class="opt">6 Monate</span><span class="opt">12 Monate</span></div>
        <div class="entry-row"><span class="lbl">Terminart:</span><span class="opt">Regulärer Termin</span><span class="opt">Kompakttermin</span></div>
        <div class="stamp-row"><span class="pill">Datum</span><span class="field"></span></div>
        <div class="stamp-row"><span class="pill">Stempel</span><span class="field"></span></div>
      </div>
      <div class="entry">
        <p class="entry-title">Nächster Termin:</p>
        <div class="entry-row"><span class="lbl">Intervall:</span><span class="opt">3 Monate</span><span class="opt">4 Monate</span><span class="opt">6 Monate</span><span class="opt">12 Monate</span></div>
        <div class="entry-row"><span class="lbl">Terminart:</span><span class="opt">Regulärer Termin</span><span class="opt">Kompakttermin</span></div>
        <div class="stamp-row"><span class="pill">Datum</span><span class="field"></span></div>
        <div class="stamp-row"><span class="pill">Stempel</span><span class="field"></span></div>
      </div>
    </div>
  </article>
</section>

<!-- pages 08 / 09 -->
<section class="panel spread">
  <article class="page left">
    <span class="page-no">08</span>
    <div class="entries full">
      <div class="entry">
        <p class="entry-title">Nächster Termin:</p>
        <div class="entry-row"><span class="lbl">Intervall:</span><span class="opt">3 Monate</span><span class="opt">4 Monate</span><span class="opt">6 Monate</span><span class="opt">12 Monate</span></div>
        <div class="entry-row"><span class="lbl">Terminart:</span><span class="opt">Regulärer Termin</span><span class="opt">Kompakttermin</span></div>
        <div class="stamp-row"><span class="pill">Datum</span><span class="field"></span></div>
        <div class="stamp-row"><span class="pill">Stempel</span><span class="field"></span></div>
      </div>
      <div class="entry">
        <p class="entry-title">Nächster Termin:</p>
        <div class="entry-row"><span class="lbl">Intervall:</span><span class="opt">3 Monate</span><span class="opt">4 Monate</span><span class="opt">6 Monate</span><span class="opt">12 Monate</span></div>
        <div class="entry-row"><span class="lbl">Terminart:</span><span class="opt">Regulärer Termin</span><span class="opt">Kompakttermin</span></div>
        <div class="stamp-row"><span class="pill">Datum</span><span class="field"></span></div>
        <div class="stamp-row"><span class="pill">Stempel</span><span class="field"></span></div>
      </div>
      <div class="entry">
        <p class="entry-title">Nächster Termin:</p>
        <div class="entry-row"><span class="lbl">Intervall:</span><span class="opt">3 Monate</span><span class="opt">4 Monate</span><span class="opt">6 Monate</span><span class="opt">12 Monate</span></div>
        <div class="entry-row"><span class="lbl">Terminart:</span><span class="opt">Regulärer Termin</span><span class="opt">Kompakttermin</span></div>
        <div class="stamp-row"><span class="pill">Datum</span><span class="field"></span></div>
        <div class="stamp-row"><span class="pill">Stempel</span><span class="field"></span></div>
      </div>
    </div>
    <span class="page-url">www.zahnpflege-am-lindenbogen.de</span>
  </article>
  <article class="page right">
    <span class="page-no">09</span>
    <div class="entries full">
      <div class="entry">
        <p class="entry-title">Nächster Termin:</p>
        <div class="entry-row"><span class="lbl">Intervall:</span><span class="opt">3 Monate</span><span class="opt">4 Monate</span><span class="opt">6 Monate</span><span class="opt">12 Monate</span></div>
        <div class="entry-row"><span class="lbl">Terminart:</span><span class="opt">Regulärer Termin</span><span class="opt">Kompakttermin</span></div>
        <div class="stamp-row"><span class="pill">Datum</span><span class="field"></span></div>
        <div class="stamp-row"><span class="pill">Stempel</span><span class="field"></span></div>
      </div>
      <div class="entry">
        <p class="entry-title">Nächster Termin:</p>
        <div class="entry-row"><span class="lbl">Intervall:</span><span class="opt">3 Monate</span><span class="opt">4 Monate</span><span class="opt">6 Monate</span><span class="opt">12 Monate</span></div>
        <div class="entry-row"><span class="lbl">Terminart:</span><span class="opt">Regulärer Termin</span><span class="opt">Kompakttermin</span></div>
        <div class="stamp-row"><span class="pill">Datum</span><span class="field"></span></div>
        <div class="stamp-row"><span class="pill">Stempel</span><span class="field"></span></div>
      </div>
      <div class="entry">
        <p class="entry-title">Nächster Termin:</p>
        <div class="entry-row"><span class="lbl">Intervall:</span><span class="opt">3 Monate</span><span class="opt">4 Monate</span><span class="opt">6 Monate</span><span class="opt">12 Monate</span></div>
        <div class="entry-row"><span class="lbl">Terminart:</span><span class="opt">Regulärer Termin</span><span class="opt">Kompakttermin</span></div>
        <div class="stamp-row"><span class="pill">Datum</span><span class="field"></span></div>
        <div class="stamp-row"><span class="pill">Stempel</span><span class="field"></span></div>
      </div>
    </div>
  </article>
</section>

</body>
</html>
```